Retail Jewelry Business Card Design Project

We are in need of a new business card design for a retail jewelry store. This store is in the business of fine jewelry including but not specific to bridal jewelry, diamonds, designer jewelry and watches.

This store has been in business for 20 years but continues to strive for a modern professional appeal. The main colors use for this business are a royal blue, white and silver.

Target Market(s)

Target market is ages 18-50

Industry/Entity Type

Jewelry

Requirements
Must have
• Sales Person Name
Sales Person Email Address

Store Address
Store Phone
Website

Standard business card size. No odd shapes or sizes.
Nice to have
• Overall modern feel for card.

We have thought that a design with a nice feature of the logo on the back of the card would be nice but open to ideas.
Should not have
• No specific images of jewelry should be used.

```html
<!DOCTYPE html>
<html lang="en">
<head>
<meta charset="utf-8">
<title>Marlow Hayes Fine Jewelry – Business Cards</title>
<link href="https://fonts.googleapis.com/css2?family=Tinos:ital,wght@0,400;0,700;1,700&family=Arimo&display=swap" rel="stylesheet">
<style>
  :root {
    --royal-blue: #2a2f9c;
    --rule-blue: #6f6fc0;
    --silver: #b9bcc4;
    --ink: #3a3a3a;
    --grey-text: #555;
    --paper: #ffffff;
    --backdrop: #eceef1;
  }
  * { margin: 0; padding: 0; box-sizing: border-box; }
  html, body {
    width: 1200px; height: 804px; overflow: hidden;
    background: var(--backdrop);
  }
  .sheet {
    position: relative; width: 1200px; height: 804px;
    display: flex; align-items: center; justify-content: center; gap: 40px;
  }
  .card {
    position: relative; width: 540px; height: 309px;
    background: var(--paper);
    box-shadow: 0 2px 10px rgba(0,0,0,0.12);
    overflow: hidden;
    font-family: 'Tinos', 'Times New Roman', serif;
  }
  .wordmark {
    position: absolute; color: var(--royal-blue);
    font-family: 'Tinos', 'Times New Roman', serif; font-weight: 700;
    text-align: center; line-height: 1.05; letter-spacing: 0.04em;
  }
  .wordmark .line-1 { display: block; font-size: 40px; }
  .wordmark .line-2 { display: block; font-size: 22px; letter-spacing: 0.16em; text-transform: uppercase; }

  /* contact side */
  .card--contact .wordmark { left: 70px; top: 34px; width: 330px; }
  .address {
    position: absolute; left: 60px; top: 160px; width: 218px;
    font-size: 13px; line-height: 1.7; color: var(--ink); text-align: right;
  }
  .divider {
    position: absolute; left: 296px; top: 124px; width: 1px; height: 72px;
    background: var(--silver);
  }
  .contact-list {
    position: absolute; left: 310px; top: 126px; list-style: none;
    font-size: 12.5px; color: var(--ink); line-height: 1.75;
  }
  .contact-list li { display: flex; align-items: center; gap: 7px; }
  .contact-list svg { width: 11px; height: 11px; flex: none; }
  .band-rule {
    position: absolute; left: 0; right: 0; top: 222px; height: 2px;
    background: var(--royal-blue);
  }
  .name-band {
    position: absolute; left: 0; right: 0; top: 230px; height: 34px;
    background: var(--royal-blue);
  }
  .salesperson {
    position: absolute; right: 40px; top: 6px;
    color: var(--paper); font-style: italic; font-weight: 700;
    font-size: 17px; letter-spacing: 0.03em;
  }

  /* logo side */
  .card--logo .wordmark { left: 0; right: 0; top: 92px; }
  .card--logo .wordmark .line-1 { font-size: 50px; }
  .card--logo .wordmark .line-2 { font-size: 26px; }
  .website {
    position: absolute; left: 0; right: 0; top: 222px; text-align: center;
    font-family: 'Arimo', Arial, sans-serif; font-size: 14px;
    letter-spacing: 0.2em; color: var(--grey-text);
  }
</style>
</head>
<body>
<main class="sheet">
  <section class="card card--contact" aria-label="Card front with contact details">
    <div class="wordmark"><span class="line-1">Marlow Hayes</span><span class="line-2">Fine Jewelry</span></div>
    <p class="address">2278 Larkspur Avenue<br>Bay Harbor, FL 32899</p>
    <div class="divider"></div>
    <ul class="contact-list">
      <li>
        <svg viewBox="0 0 12 12" aria-hidden="true"><circle cx="6" cy="6" r="6" fill="var(--royal-blue)"/><path d="M4 3.2c.4-.3.8-.2 1 .2l.4.9c.1.3 0 .5-.2.7l-.3.3c.3.7.9 1.3 1.6 1.6l.3-.3c.2-.2.4-.3.7-.2l.9.4c.4.2.5.6.2 1-.5.7-1.2.8-2 .4C5.3 7.6 4.4 6.7 3.8 5.4c-.4-.8-.3-1.6.2-2.2z" fill="#fff"/></svg>
        555-214-7730
      </li>
      <li>
        <svg viewBox="0 0 12 12" aria-hidden="true"><circle cx="6" cy="6" r="6" fill="var(--royal-blue)"/><rect x="3" y="4" width="6" height="4.2" fill="#fff"/><path d="M3 4l3 2.3L9 4" stroke="var(--royal-blue)" stroke-width=".7" fill="none"/></svg>
        marlow@marlowhayesjewelry.com
      </li>
      <li>
        <svg viewBox="0 0 12 12" aria-hidden="true"><circle cx="6" cy="6" r="6" fill="var(--royal-blue)"/><circle cx="6" cy="6" r="3.2" stroke="#fff" stroke-width=".8" fill="none"/><path d="M2.8 6h6.4M6 2.8c-1.4 1.8-1.4 4.6 0 6.4M6 2.8c1.4 1.8 1.4 4.6 0 6.4" stroke="#fff" stroke-width=".7" fill="none"/></svg>
        www.marlowhayesjewelry.com
      </li>
    </ul>
    <div class="band-rule"></div>
    <div class="name-band"><span class="salesperson">Marlow Hayes Bennett</span></div>
  </section>

  <section class="card card--logo" aria-label="Card back with store name">
    <div class="wordmark"><span class="line-1">Marlow Hayes</span><span class="line-2">Fine Jewelry</span></div>
    <p class="website">www.marlowhayesjewelry.com</p>
  </section>
</main>
</body>
</html>
```